Brookvane Consulting Business Card Design

Business Card Design for Brookvane Consulting. Brookvane Consulting is a boutique consultancy based in Atlanta, GA., that specializes in marketing strategy, organization planning, and leadership development. We provide solutions for small businesses and startups as well as Vantage 300 companies.

http://brookvaneconsulting.com/

Target Market(s)

We provide solutions for small businesses and startups as well as Vantage 300 companies.

Industry/Entity Type

Consulting

Contact Information for Business Card

Two sided business card with priority on contact information, logo, tag line (Inspiration to Dream More, Do More, Become More)

Colors

Designer to choose colors to be used in the design.

Requirements
Must have
• contact information, logo, tag line (Inspiration to Dream More, Do More, Become More)
• Simple no over communication.
Nice to have
• I would like to see different placements of logo and creative use of both sides of the card
Should not have
• Do not put too much information on the card.

```html
<!DOCTYPE html>
<html lang="en">
<head>
<meta charset="utf-8">
<title>Brookvane Consulting – Business Card</title>
<link rel="stylesheet" href="https://fonts.googleapis.com/css2?family=Lato:wght@300;400&family=Pacifico&display=swap">
<style>
  :root {
    --backdrop: #3a332f;
    --card: #141414;
    --card-edge: #1c1c1c;
    --pattern-a: #1a1a1a;
    --pattern-b: #232323;
    --ink: #f2f2f2;
    --ink-soft: #cfcfcf;
  }
  * { margin: 0; padding: 0; box-sizing: border-box; }
  html, body { width: 1200px; height: 769px; overflow: hidden; }
  body {
    background: var(--backdrop);
    display: flex;
    align-items: center;
    justify-content: center;
    gap: 40px;
    font-family: "Lato", sans-serif;
  }
  .card {
    position: relative;
    width: 520px;
    height: 297px;
    background: var(--card);
    border: 1px solid var(--card-edge);
    box-shadow: 0 18px 40px rgba(0,0,0,.45);
    color: var(--ink);
    overflow: hidden;
  }
  /* back side: contact details over a pattern area */
  .card-back .pattern-area {
    position: absolute;
    inset: 0;
    background: linear-gradient(135deg, var(--pattern-a), var(--pattern-b) 50%, var(--pattern-a));
  }
  .contact {
    position: absolute;
    inset: 0;
    display: flex;
    flex-direction: column;
    align-items: center;
    justify-content: center;
    text-align: center;
  }
  .contact-name {
    font-family: "Pacifico", cursive;
    font-size: 24px;
    line-height: 1.1;
  }
  .contact-role {
    font-size: 15px;
    font-weight: 400;
    margin-top: 2px;
  }
  .contact-rule {
    width: 26px;
    height: 1.5px;
    background: var(--ink);
    margin: 12px 0 14px;
  }
  .contact-line {
    font-size: 14px;
    line-height: 1.45;
    color: var(--ink-soft);
  }
  /* front side: brand name and tagline */
  .card-front {
    display: flex;
    flex-direction: column;
    align-items: center;
    justify-content: center;
  }
  .brand {
    display: flex;
    align-items: center;
    gap: 12px;
  }
  .brand-mark {
    width: 18px;
    height: 18px;
    border: 1.5px solid var(--ink);
  }
  .brand-name {
    font-size: 34px;
    font-weight: 300;
    letter-spacing: .06em;
    text-transform: uppercase;
  }
  .tagline {
    margin-top: 26px;
    font-size: 14px;
    font-weight: 400;
    color: var(--ink-soft);
    letter-spacing: .02em;
  }
</style>
</head>
<body>
  <section class="card card-back">
    <div class="pattern-area" role="img" aria-label="Subtle dark geometric pattern of rectangles and small triangles"></div>
    <div class="contact">
      <p class="contact-name">Darius Holloway</p>
      <p class="contact-role">Founder/Managing Director</p>
      <span class="contact-rule"></span>
      <p class="contact-line">424-555-0187</p>
      <p class="contact-line">darius@brookvaneconsulting.com</p>
      <p class="contact-line">brookvaneconsulting.com</p>
    </div>
  </section>

  <section class="card card-front">
    <div class="brand">
      <span class="brand-mark"></span>
      <span class="brand-name">Brookvane Consulting</span>
    </div>
    <p class="tagline">Inspiration to Dream More, Do More, Become More</p>
  </section>
</body>
</html>
```